Suchen ansprechendes & seriöses Urkunden/Zertifikat Design für Webseite & Druck
Zielgruppe
Auf unserer Webseite http://wacker-im-alter.de können sich Unternehmen, Institutionen und Vereine ihre Seniorenfreundlichkeit durch ein Zertifikat bestätigen und zertifizieren lassen.
Unsere Kundengruppen: Hotel – Gastronomie – Wellness – Reisen und Touristik – Touristikregionen – Seniorenshop – Onlineshop – Unternehmen als Dienstleister – Medizin und Health-Service – Apotheke – Altenheim – Pflegeheim – Seniorenheim – Vereine – Seniorenservice – Zahnärzte – Fitnessstudio – Sportstudio – Physiotherapie – Sportverein – Golfclub – und viele weitere seniorenfreundliche Institutionen.
Aufgabenstellung
Auftrag- Ausschreibung:
- Erstellung eines Design:
- Urkunde für Webseite wacker-im-alter.de - Das Zertifikat "Wacker im Alter“
Funktion:
Kunde erkennt das Zertifikat - Logo auf einer Webseite und Klickt auf dieses.
Er wird weitergeleitet auf eine Unterseite, worin die Richtlinien und die Urkunde sichtbar wird.
Zielgruppe:
- Unternehmen, welche das Zertifikat auf Ihre Webseite setzen. Die Urkunde gibt Auskunft, dass der Dienstleister einen besonderen Service für Senioren ausübt. Die Urkunde ist sichtbar auf der Webseite, indem das Logo angeklickt wird. Die Urkunde gibt es ebenfalls als Download, damit der Kunde diese in seinen Geschäftsräumen aufhängen kann oder diese in seinen Werbeunterlagen präsentieren kann.
- Verbraucher sollen beeindruckt sein, von der Urkunde, welches Vertrauen ausstrahlt, aber auch Seriosität
Folgende Ausstrahlung soll die Urkunde haben:
- Soll Mitbewerber des Zertifikatsinhaber beeindrucken und das Verlangen aufzeigen, sich ebenfalls zertifizieren zu lassen ( ca: 70% der Kunden sind Mitbewerber … ). Nach dem Motto "Das Logo ist super und edel, das muss ich auch haben!"
- Der Kunde als Verbraucher soll Vertrauen gewinnen, die Daten sollen gut sichtbar sein, aber nicht verkitscht wie eine Urkunde bei einer Kaffeefahrt. Der Verbraucher geht auf das Zertifikat und kommt zur Urkunde, deshalb soll die Farbe, und Darstellung, Seriosität des Unternehmens ausstrahlen.
Sonstiges
- Die Urkunde soll dem neuen Design unserer Seite (zu sehen unter: http://gutsiegel-pruefung.de) angepasst sein.
- Vor Auftragsendvergabe erhalten Sie noch ein telefonisches Briefing über unsere Erfahrungswerte
Link zur bestehenden alten Webseite (Altes Design): http://wacker-im-alter.de
Info Verbraucher: http://www.wacker-im-alter.de/verbraucher/
Info zum Zertifikat: http://www.wacker-im-al..

```html
<!DOCTYPE html>
<html lang="de">
<head>
<meta charset="utf-8">
<title>Zertifikat – Wacker im Alter</title>
<link rel="stylesheet" href="https://fonts.googleapis.com/css2?family=Raleway:wght@200;300;400;500;600&display=swap">
<style>
  :root {
    --paper: #f7f7f7;
    --pinstripe: #e6e6e6;
    --frame: #b9a58a;
    --frame-light: #d8ccba;
    --title: #5b4c3f;
    --label: #8c7458;
    --value: #4f4f4f;
    --ribbon: #ebe5da;
    --ribbon-shade: #d2c7b5;
    --ribbon-text: #4a3d31;
    --laurel: #ece8e1;
    --badge: #d6d6d6;
    --stripe-red: #c0392b;
    --stripe-blue: #2d3f8f;
    --signature: #dcdcdc;
  }
  * { margin: 0; padding: 0; box-sizing: border-box; }
  html, body { width: 850px; height: 1200px; overflow: hidden; }
  body {
    position: relative;
    font-family: "Raleway", sans-serif;
    background: repeating-linear-gradient(90deg, var(--paper) 0 4px, var(--pinstripe) 4px 5px);
  }
  .edge-stripes { position: absolute; left: 0; top: 0; width: 28px; height: 1200px;
    background: linear-gradient(90deg, var(--stripe-red) 0 10px, #fff 10px 17px, var(--stripe-blue) 17px 27px, transparent 27px); }
  .page-number { position: absolute; left: 28px; top: 1160px; transform: rotate(-90deg); transform-origin: left top;
    font-size: 15px; font-weight: 600; color: var(--title); }
  .frame-outer { position: absolute; left: 68px; top: 27px; width: 752px; height: 1146px; border: 1px solid var(--frame); }
  .frame-inner { position: absolute; left: 87px; top: 70px; width: 716px; height: 1028px;
    border-left: 1px solid var(--frame); border-right: 1px solid var(--frame); }
  .hatch-band { position: absolute; left: 90px; width: 710px; height: 13px;
    background: repeating-linear-gradient(45deg, var(--frame-light) 0 1px, transparent 1px 5px);
    border-top: 1px solid var(--frame); border-bottom: 1px solid var(--frame); }
  .hatch-band.top { top: 46px; }
  .hatch-band.bottom { top: 1108px; }
  .band-diamond { position: absolute; left: 50%; top: 50%; width: 12px; height: 12px; margin: -6px 0 0 -6px;
    background: var(--frame); transform: rotate(45deg); }
  .laurel { position: absolute; left: 255px; top: 92px; width: 340px; height: 285px; border-radius: 50%;
    background: radial-gradient(ellipse at center, transparent 45%, var(--laurel) 62%, transparent 75%); }
  .title { position: absolute; left: 0; width: 850px; top: 118px; text-align: center;
    font-size: 106px; font-weight: 200; letter-spacing: 3px; color: var(--title); line-height: 1; }
  .ribbon { position: absolute; left: 165px; top: 244px; width: 502px; height: 118px; }
  .row { position: absolute; left: 0; width: 850px; font-size: 21px; line-height: 29px; }
  .row .label { position: absolute; right: 500px; text-align: right; font-weight: 600; color: var(--label); }
  .row .value { position: absolute; left: 359px; font-weight: 400; color: var(--value); }
  .badge { position: absolute; left: 512px; top: 782px; width: 240px; height: 240px; border-radius: 50%;
    background: var(--badge); }
  .signature { position: absolute; top: 1000px; height: 62px; background: var(--signature); opacity: .5; border-radius: 8px; }
  .signature.first { left: 330px; width: 120px; }
  .signature.second { left: 490px; width: 160px; }
  .signer { position: absolute; top: 1067px; font-size: 15px; color: var(--value); }
</style>
</head>
<body>
  <div class="edge-stripes"></div>
  <div class="page-number">26</div>

  <div class="frame-outer"></div>
  <div class="frame-inner"></div>
  <div class="hatch-band top"><span class="band-diamond"></span></div>
  <div class="hatch-band bottom"><span class="band-diamond"></span></div>

  <div class="laurel" role="img" aria-label="Dezenter Lorbeerkranz im Hintergrund"></div>
  <h1 class="title">ZERTIFIKAT</h1>

  <svg class="ribbon" viewBox="0 0 502 118" aria-label="Wacker im Alter">
    <path d="M4,84 L56,70 L56,112 L4,118 L24,100 Z" fill="var(--ribbon-shade)"/>
    <path d="M498,84 L446,70 L446,112 L498,118 L478,100 Z" fill="var(--ribbon-shade)"/>
    <path d="M46,62 Q251,-8 456,62 L456,104 Q251,36 46,104 Z" fill="var(--ribbon)" stroke="var(--ribbon-shade)" stroke-width="1"/>
    <path id="ribbon-curve" d="M60,92 Q251,28 442,92" fill="none"/>
    <text font-family="Raleway, sans-serif" font-size="29" font-weight="500" fill="var(--ribbon-text)" letter-spacing="1.5">
      <textPath href="#ribbon-curve" startOffset="50%" text-anchor="middle">WACKER IM ALTER</textPath>
    </text>
  </svg>

  <div class="details">
    <div class="row" style="top:415px"><span class="label">Zertifikat ID:</span><span class="value">7250441e9e</span></div>
    <div class="row" style="top:475px"><span class="label">Anbieter:</span><span class="value">Wacker im Alter<br>Ihr Zertifizierungsdienst</span></div>
    <div class="row" style="top:556px"><span class="label">Status:</span><span class="value">aktiv</span></div>
    <div class="row" style="top:613px"><span class="label">Unternehmen:</span><span class="value">Senioren Service Lindholm<br>Ahornweg 7<br>54321 Musterort<br>Deutschland<br>info@lindholm.org</span></div>
    <div class="row" style="top:789px"><span class="label">Vertretungs-<br>berechtigter:</span><span class="value">Frau Greta<br>Lindholm</span></div>
    <div class="row" style="top:880px"><span class="label">Erstprüfung am:</span><span class="value">07.04.2017</span></div>
    <div class="row" style="top:918px"><span class="label">gültig bis:</span><span class="value">07.04.2019</span></div>
    <div class="row" style="top:1062px"><span class="label">Bestätigt von:</span></div>
  </div>

  <div class="badge" role="img" aria-label="Prüfsiegel des Zertifizierungsdienstes"></div>

  <div class="signature first" role="img" aria-label="Handschriftliche Unterschrift"></div>
  <div class="signature second" role="img" aria-label="Handschriftliche Unterschrift"></div>
  <span class="signer" style="left:367px">K. Hartmann</span>
  <span class="signer" style="left:500px">L. Brenner</span>
</body>
</html>
```